Lantern Co. Supplement General Packaging Design

I am looking for a design template to design all of my various supplements and other products around. Meaning that this design should be able to just be able to change around words, up to a few small images, and text to suit my other various products.

The brand name is Lantern Co. and the slogan is: Heros Are Made
This is For an Apple Cider Vinegar Gummy, and include these top three things: Vegan, Gluten Free, Non-GMO somewhere in the design.

I want the design to have a luxurious feel. With some kind of design element where the logo is sort of the secondary aspect of the design.

Target Market(s)

Men age 24-45

Industry/Entity Type

Supplement

Requirements
Must have
• MUST HAVE A "vintage" LOOK AND FEEL. MUST HAVE ANOTHER design element besides the logo. (Something Vintage) MUST USE THE PROVIDED TEMPLATE A PDF IN THE FILES BELOW LABELED " TEMPLATE" and the LOGO PROVIDED under "Lantern Co. 2" OR "lantern co.3" whichever is better suited for the design. Bold design. Another color besides black to stand out. Use the lantern co logo which is below in the provided images. The design should go around the logo and fit the same aesthetic. The rest are for inspiration, what I like.

```html
<!DOCTYPE html>
<html lang="en">
<head>
<meta charset="utf-8">
<title>Lantern Co. Apple Cider Vinegar Gummy Label</title>
<link href="https://fonts.googleapis.com/css2?family=Sancreek&family=Oswald:wght@500;600&family=Arimo:wght@400;700&family=Archivo+Black&display=swap" rel="stylesheet">
<style>
  :root{
    --page:#ffffff;
    --paper:#d9d7cb;
    --band:#4d6f7d;
    --ink:#151515;
    --panel:#1a1c1d;
    --frame-bg:#1f282b;
    --frame-line:#cfc9b6;
    --teal:#5a8293;
    --cream:#ece5d2;
    --rust:#b8432f;
  }
  *{box-sizing:border-box;margin:0;padding:0}
  html,body{width:1200px;height:1200px;overflow:hidden;background:var(--page)}
  .label{position:absolute;left:20px;top:380px;width:1160px;height:440px;background:var(--paper);overflow:hidden}
  .band{position:absolute;left:0;right:0;height:8px;background:var(--band)}
  .band.top{top:14px}.band.bottom{bottom:14px}

  .directions{position:absolute;left:0;top:0;width:300px;height:100%;padding:34px 22px 0 24px;font-family:Arimo,Arial,sans-serif;font-size:11px;line-height:1.35;color:var(--ink)}
  .directions p{margin-bottom:14px;text-align:justify}
  .fda-box{border:1px solid var(--ink);padding:8px 10px;font-size:12.5px;margin-bottom:12px}
  .maker-box{border:1px solid var(--ink);background:#fff;padding:8px 12px;margin-top:6px;font-size:12px;text-align:center}

  .panel{position:absolute;left:300px;top:26px;width:560px;height:388px;background:var(--panel);
    clip-path:polygon(2% 0,98% 0,100% 6%,99% 14%,100% 26%,98.6% 40%,100% 55%,99% 70%,100% 85%,98.5% 100%,1.5% 100%,0 88%,1% 72%,0 58%,1.4% 42%,0 28%,1% 12%,0 4%)}
  .claims{position:absolute;top:80px;display:flex;flex-direction:column;gap:22px}
  .claims.left{left:26px}.claims.right{right:26px}
  .claim{width:62px;height:62px;border-radius:50%;border:2px solid var(--frame-line);display:flex;align-items:center;justify-content:center;text-align:center;
    font-family:Oswald,sans-serif;font-weight:500;font-size:9.5px;letter-spacing:1px;color:var(--frame-line);line-height:1.1}

  .frame{position:absolute;left:110px;top:10px;width:340px;height:368px;border:3px double var(--frame-line);padding:8px}
  .frame-inner{position:relative;width:100%;height:100%;border:1px solid var(--teal);background:var(--frame-bg);
    display:flex;flex-direction:column;align-items:center;padding-top:34px;color:var(--cream)}
  .brand-name{font-family:Oswald,sans-serif;font-weight:600;font-size:26px;letter-spacing:1px;color:var(--cream)}
  .title{font-family:Sancreek,serif;font-weight:400;color:var(--cream);text-shadow:3px 3px 0 var(--rust);text-align:center;line-height:1;white-space:nowrap}
  .title .line1{font-size:44px;margin-top:28px;display:block}
  .title .line2{font-size:36px;margin-top:18px;display:block}
  .title .line3{font-size:26px;margin-top:4px;display:block}
  .count{font-family:Oswald,sans-serif;font-size:12px;letter-spacing:2px;margin-top:34px}
  .ribbon{margin-top:6px;background:var(--teal);color:var(--cream);font-family:Oswald,sans-serif;font-size:12px;letter-spacing:2px;padding:4px 18px}

  .facts{position:absolute;left:872px;top:34px;width:272px;border:2px solid var(--ink);background:#f2f0e8;padding:6px 8px;font-family:Arimo,Arial,sans-serif;color:var(--ink)}
  .facts h2{font-family:"Archivo Black",Arial,sans-serif;font-size:20px;text-align:center;font-weight:400}
  .facts .serving{font-weight:700;font-size:11px;border-bottom:6px solid var(--ink);padding:3px 0 4px}
  .facts table{width:100%;border-collapse:collapse;font-size:10.5px}
  .facts th{font-size:8.5px;text-align:right;padding:3px 0;border-bottom:3px solid var(--ink)}
  .facts td{border-bottom:1px solid var(--ink);padding:2px 0}
  .facts td.amt,.facts td.dv{text-align:right;font-size:8.5px;white-space:nowrap;padding-left:4px}
  .facts .indent{padding-left:10px}.facts .indent2{padding-left:20px}
  .facts .notes{font-size:9.5px;padding-top:4px;border-top:4px solid var(--ink);margin-top:-1px}
</style>
</head>
<body>
<div class="label">
  <div class="band top"></div>
  <div class="band bottom"></div>

  <section class="directions">
    <p><b>Suggested Use:</b> Take one (1) gummy daily or as directed by a healthcare professional.</p>
    <p><b>Caution:</b> If you are pregnant, nursing, taking any medications or have any medical condition, consult your doctor before use. Discontinue use and consult your doctor if any adverse reactions occur.</p>
    <p>KEEP OUT OF REACH OF CHILDREN. STORE AT ROOM TEMPERATURE.</p>
    <p>ALLERGEN WARNING: This product contains tree nuts (coconut).</p>
    <div class="fda-box">†These statements have not been evaluated by the FDA. This product is not intended to diagnose, cure, treat or prevent any disease.</div>
    <div>Manufactured for:</div>
    <div class="maker-box">Manufactured for Northfield</div>
  </section>

  <section class="panel">
    <div class="claims left">
      <div class="claim">DETOX</div>
      <div class="claim">IMMUNE<br>HEALTH</div>
      <div class="claim">WEIGHT<br>MGMT</div>
    </div>
    <div class="frame">
      <div class="frame-inner">
        <div class="brand-name">LANTERN CO.</div>
        <h1 class="title">
          <span class="line1">APPLE CIDER</span>
          <span class="line2">VINEGAR</span>
          <span class="line3">GUMMY</span>
        </h1>
        <div class="count">60 GUMMIES</div>
        <div class="ribbon">DIETARY SUPPLEMENT</div>
      </div>
    </div>
    <div class="claims right">
      <div class="claim">GMO<br>FREE</div>
      <div class="claim">GLUTEN<br>FREE</div>
      <div class="claim">VEGAN</div>
    </div>
  </section>

  <section class="facts">
    <h2>Supplement Facts</h2>
    <div class="serving">Serving Size: 1 Gummy<br>Servings Per Container: 60</div>
    <table>
      <tr><th colspan="2">Amount Per Serving</th><th>% DV</th></tr>
      <tr><td>Calories</td><td class="amt">10</td><td class="dv"></td></tr>
      <tr><td>Total Carbohydrates</td><td class="amt">3 g</td><td class="dv">&lt;1%</td></tr>
      <tr><td class="indent">Total Sugars</td><td class="amt">2 g</td><td class="dv">**</td></tr>
      <tr><td class="indent2">Includes 2 g Added Sugars</td><td class="amt"></td><td class="dv">4%</td></tr>
      <tr><td>Vitamin B-6 (as Pyridoxine HCl)</td><td class="amt">0.5 mg</td><td class="dv">29%</td></tr>
      <tr><td>Folate (120 mcg Folic Acid)</td><td class="amt">200 mcg DFE</td><td class="dv">50%</td></tr>
      <tr><td>Vitamin B-12 (as Cyanocobalamin)</td><td class="amt">1.2 mcg</td><td class="dv">50%</td></tr>
      <tr><td>Iodine (as Potassium Iodide)</td><td class="amt">50 mcg</td><td class="dv">33%</td></tr>
      <tr><td>Apple Cider Vinegar Powder (fruit)<br>(providing 5% total acid)</td><td class="amt">500 mg</td><td class="dv">**</td></tr>
      <tr><td>Pomegranate Juice Powder</td><td class="amt">40 mcg</td><td class="dv">**</td></tr>
      <tr><td>Beet Root Juice Powder</td><td class="amt">40 mcg</td><td class="dv">**</td></tr>
    </table>
    <div class="notes">* % Daily Value Based on 2,000 Calorie Diet<br>** Daily Value Not Established</div>
  </section>
</div>
</body>
</html>
```